Freelance business trainer needs a new business card

My business is called Brontlearn. I provide training in the workplace on management, coaching and mentoring, and customer service topics for a variety of businesses, colleges and private training providers, and teach on management programs. I need a professional but eye catching business card. Business colours grey and orange. My name Marion Tadwick; Tel 07382 415067; email mtadwick@brontlearn.co.uk; website www.brontlearn.co.uk.
Happy to have some sort of logo on front and details on back or all on one side
Target Market(s)
SME businesses and colleges - workshops i run are for adults in the workplace
Industry/Entity Type
Training
Look and feel

```html
<!DOCTYPE html>
<html lang="en">
<head>
<meta charset="utf-8">
<title>Brontlearn Business Card</title>
<link rel="stylesheet" href="https://fonts.googleapis.com/css2?family=Ubuntu:wght@300;400;500;700&display=swap">
<style>
  :root {
    --orange: #f7901e;
    --orange-soft: #f9a44a;
    --grey: #6e6e6e;
    --grey-dark: #5f5f5f;
    --grey-light: #7b7b7b;
    --white: #f4f4f4;
    --backdrop: #d9dadc;
    --ink-light: #ffffff;
  }
  * { box-sizing: border-box; margin: 0; padding: 0; }
  html, body {
    width: 1200px; height: 800px; overflow: hidden;
    background: var(--backdrop);
    font-family: "Ubuntu", sans-serif;
  }
  .canvas { position: relative; width: 1200px; height: 800px; }

  .card {
    position: absolute; overflow: hidden;
    border-radius: 26px;
    box-shadow: 0 6px 18px rgba(0,0,0,0.18);
  }

  /* Front: portrait orange side */
  .card-front {
    left: 110px; top: 140px; width: 320px; height: 520px;
    background: var(--orange);
  }
  .card-front .edge-band {
    position: absolute; left: 0; top: 0; bottom: 0; width: 38px;
    background: var(--white);
  }
  .card-front .edge-rule {
    position: absolute; left: 38px; top: 0; bottom: 0; width: 6px;
    background: var(--grey);
  }
  .halo {
    position: absolute; border-radius: 50%;
    background: rgba(255,255,255,0.12);
  }
  .card-front .halo-top { width: 300px; height: 300px; left: 120px; top: -90px; }
  .card-front .halo-mid { width: 300px; height: 300px; left: 30px; top: 150px; background: rgba(0,0,0,0.04); }
  .card-front .tagline {
    position: absolute; left: 62px; top: 90px;
    writing-mode: vertical-rl;
    color: var(--ink-light); font-size: 15px; font-weight: 300; letter-spacing: 0.2px;
  }
  .card-front .brand {
    position: absolute; left: 140px; top: 110px;
    display: flex; flex-direction: column; align-items: center; gap: 14px;
  }
  .card-front .brand-name {
    writing-mode: vertical-rl;
    color: var(--grey); font-size: 64px; font-weight: 400; line-height: 1;
  }
  .card-front .brand-dot {
    width: 18px; height: 18px; border-radius: 50%; background: var(--grey);
  }

  /* Back: landscape grey side */
  .card-back {
    left: 480px; top: 210px; width: 620px; height: 380px;
    background: var(--grey);
  }
  .card-back .top-band {
    position: absolute; left: 0; right: 0; top: 0; height: 48px;
    background: var(--white);
    display: flex; align-items: center; justify-content: flex-end; padding-right: 34px;
  }
  .card-back .top-rule {
    position: absolute; left: 0; right: 0; top: 48px; height: 4px; background: var(--orange);
  }
  .card-back .website {
    color: var(--orange); font-size: 15px; font-weight: 500; letter-spacing: 4px;
  }
  .card-back .bottom-band {
    position: absolute; left: 0; right: 0; bottom: 0; height: 26px; background: var(--white);
  }
  .card-back .bottom-rule {
    position: absolute; left: 0; width: 150px; bottom: 26px; height: 4px; background: var(--orange);
  }
  .card-back .halo-a { width: 260px; height: 260px; left: 250px; top: 200px; background: rgba(255,255,255,0.07); }
  .card-back .halo-b { width: 240px; height: 240px; left: 470px; top: 230px; background: rgba(0,0,0,0.06); }

  .contact { position: absolute; left: 34px; top: 78px; color: var(--ink-light); }
  .contact .name {
    color: var(--orange); font-size: 22px; font-weight: 700; letter-spacing: 1px; text-transform: uppercase;
  }
  .contact .role, .contact .quals { font-size: 13px; font-weight: 300; margin-top: 3px; }
  .contact .lines { margin-top: 16px; font-size: 16px; font-weight: 300; line-height: 1.45; }
  .contact .label { color: var(--orange); font-size: 12px; margin-right: 6px; }

  .card-back .brand {
    position: absolute; right: 40px; top: 120px;
    display: flex; align-items: center; gap: 10px;
  }
  .card-back .brand-name { color: var(--ink-light); font-size: 50px; font-weight: 400; line-height: 1; }
  .card-back .brand-dot { width: 16px; height: 16px; border-radius: 50%; background: var(--orange); }

  .address {
    position: absolute; left: 300px; top: 230px;
    color: var(--ink-light); font-size: 17px; font-weight: 300; line-height: 1.35;
    font-style: normal;
  }
</style>
</head>
<body>
<main class="canvas">

  <section class="card card-front" aria-label="Business card front">
    <div class="edge-band"></div>
    <div class="edge-rule"></div>
    <div class="halo halo-top"></div>
    <div class="halo halo-mid"></div>
    <p class="tagline">Management, Business &amp; Customer Service Training</p>
    <div class="brand">
      <span class="brand-name">Brontlearn</span>
      <span class="brand-dot"></span>
    </div>
  </section>

  <section class="card card-back" aria-label="Business card back">
    <div class="halo halo-a"></div>
    <div class="halo halo-b"></div>
    <div class="top-band"><span class="website">www.brontlearn.co.uk</span></div>
    <div class="top-rule"></div>

    <div class="contact">
      <h1 class="name">Marion Tadwick</h1>
      <p class="role">Owner/Lead Trainer</p>
      <p class="quals">MCMI, MIfL, CertEd, PGCCM, TIOSH</p>
      <p class="lines">
        <span class="label">[T]</span>07382 415067<br>
        <span class="label">[E]</span>mtadwick@brontlearn.co.uk
      </p>
    </div>

    <div class="brand">
      <span class="brand-name">Brontlearn</span>
      <span class="brand-dot"></span>
    </div>

    <address class="address">
      Maple Court<br>
      Barlow Lane<br>
      Wendle<br>
      WN14 3QT
    </address>

    <div class="bottom-rule"></div>
    <div class="bottom-band"></div>
  </section>

</main>
</body>
</html>
```